Business Card Design for Training Business

Clear Path Coaching is a new business that delivers training and other services with a focus on topics related to mental health and wellbeing, for example, Wellmind Response Course, Resilience etc. We have a strong focus on evidence-based psychology and neuroscience. I have a logo which I will upload with the brief, so please consider colours that work well with the logo.
Target Market(s)
Adults, workplaces (particularly government and not-for-profits)
Industry/Entity Type
Business
Contact Information for Business Card
Head Strong TrainingSamantha SellwoodDirector0438 770 850sam@headstrongtraining.com.auwww.headstrongtraining.com.au

```html
<!DOCTYPE html>
<html lang="en">
<head>
<meta charset="utf-8">
<title>Clear Path Coaching – Business Card</title>
<link href="https://fonts.googleapis.com/css2?family=Source+Sans+3:wght@300;400&display=swap" rel="stylesheet">
<style>
  :root {
    --page-bg: #d9d6d1;
    --card-light: #f4f3f1;
    --card-mid: #d8d4cd;
    --card-warm: #c9bfae;
    --teal-dark: #1b4c48;
    --teal-stripe: #1d6a5b;
    --teal-text: #1f5d5a;
    --ink: #2b2b2b;
    --ink-soft: #4a4a4a;
  }
  * { box-sizing: border-box; margin: 0; padding: 0; }
  html, body { width: 1200px; height: 970px; overflow: hidden; }
  body {
    background: var(--page-bg);
    font-family: "Source Sans 3", sans-serif;
    position: relative;
  }
  .business-card {
    position: absolute;
    left: 100px; top: 187px;
    width: 1000px; height: 596px;
    background:
      radial-gradient(ellipse 420px 300px at 620px 300px, var(--card-warm), transparent 70%),
      linear-gradient(120deg, var(--card-light) 0%, var(--card-mid) 55%, var(--card-warm) 100%);
    box-shadow: 0 6px 18px rgba(0,0,0,0.25);
    overflow: hidden;
  }
  .card-swoosh { position: absolute; inset: 0; }
  .brand {
    position: absolute;
    left: 78px; top: 66px;
    width: 320px;
    text-align: center;
    color: var(--ink-soft);
    font-weight: 300;
  }
  .brand-dot {
    display: block;
    width: 130px; height: 130px;
    margin: 0 auto 34px;
    border-radius: 50%;
    border: 3px solid var(--teal-stripe);
  }
  .brand-name {
    font-size: 33px;
    letter-spacing: 4px;
    line-height: 1;
  }
  .brand-sub {
    font-size: 17px;
    letter-spacing: 6px;
    margin-top: 8px;
    line-height: 1;
  }
  .person { position: absolute; left: 75px; top: 318px; }
  .person-name {
    font-size: 38px;
    color: var(--teal-text);
    font-weight: 400;
    line-height: 1.05;
  }
  .person-role {
    font-size: 24px;
    color: var(--ink);
    line-height: 1.2;
  }
  .contacts {
    position: absolute;
    left: 78px; top: 418px;
    list-style: none;
  }
  .contact {
    display: flex;
    align-items: center;
    height: 38px;
    font-size: 26px;
    color: var(--ink);
  }
  .contact-icon {
    width: 24px; height: 24px;
    margin-right: 22px;
    flex: none;
  }
</style>
</head>
<body>
  <section class="business-card">
    <svg class="card-swoosh" viewBox="0 0 1000 596" width="1000" height="596" aria-hidden="true">
      <path d="M753 0 C880 120 960 300 1000 520 L1000 0 Z" fill="var(--teal-dark)"/>
      <path d="M739 37 C860 150 925 360 930 596 L1000 596 L1000 555 C985 380 900 170 739 37 Z" fill="var(--teal-stripe)"/>
    </svg>

    <div class="brand">
      <span class="brand-dot"></span>
      <p class="brand-name">CLEAR PATH</p>
      <p class="brand-sub">COACHING</p>
    </div>

    <div class="person">
      <h1 class="person-name">Rebecca Tanfield</h1>
      <p class="person-role">Director</p>
    </div>

    <ul class="contacts">
      <li class="contact">
        <svg class="contact-icon" viewBox="0 0 24 24" aria-hidden="true">
          <rect width="24" height="24" fill="#2a2a2a"/>
          <path d="M8 5 L10 5 L11 9 L9.5 10.5 C10.5 12.5 11.5 13.5 13.5 14.5 L15 13 L19 14 L19 16 C19 17.5 17.5 19 16 19 C10 18.5 5.5 14 5 8 C5 6.5 6.5 5 8 5 Z" fill="#fff"/>
        </svg>
        0491 362 517
      </li>
      <li class="contact">
        <svg class="contact-icon" viewBox="0 0 24 24" aria-hidden="true">
          <rect width="24" height="24" fill="#2a2a2a"/>
          <rect x="5" y="7" width="14" height="10" fill="#fff"/>
          <path d="M5 7 L12 13 L19 7" fill="none" stroke="#2a2a2a" stroke-width="1.5"/>
        </svg>
        bec@clearpathcoaching.example.au
      </li>
      <li class="contact">
        <svg class="contact-icon" viewBox="0 0 24 24" aria-hidden="true">
          <rect width="24" height="24" fill="#2a2a2a"/>
          <circle cx="12" cy="12" r="7" fill="none" stroke="#fff" stroke-width="1.6"/>
          <ellipse cx="12" cy="12" rx="3" ry="7" fill="none" stroke="#fff" stroke-width="1.2"/>
          <line x1="5" y1="12" x2="19" y2="12" stroke="#fff" stroke-width="1.2"/>
        </svg>
        www.clearpathcoaching.example.au
      </li>
    </ul>
  </section>
</body>
</html>
```